I want to redesign the Tallvex corporate website

Morrowdale Farms Limited (Tallvex) is a Nigerian integrated agribusiness and premium food company operating across agriculture, food processing and nationwide FMCG distribution.
We are redesigning our corporate website to reflect our evolution into a modern, premium food company capable of serving institutional buyers, distributors, retailers, investors and consumers. The new website should feel comparable to the websites of leading global food brands — not a typical agricultural website.

Target Market(s)

Nigeria / Africa

Industry/Entity Type

FMCG

Coding

Coded - Design and coding required

Number of Pages Required

5+ page

Colors

Designer to choose colors to be used in the design.

Requirements
Must have
• The website must communicate the following attributes consistently across every page, in both design and language. Premium Quality of finish signals quality of product , Clean Uncluttered layouts, disciplined use of elements ,Modern Current design language, not dated conventions ,Innovative and Forward-looking, technology-enabled , Sustainable Responsible practice made visible Nigerian with global standards, Proudly local in origin, international in execution
Nice to have
• Lots of white space , Fast loading, Premium photography,Mobile-first,Elegant typography,Minimal clutter, Rounded elements,High-end corporate feel, Smooth curved section transitions, Soft shadows
Should not have
• The new website should feel comparable to the websites of leading global food brands — not a typical agricultural website. Also do not copy the business profile as website , its is just a guide !

```html
<!DOCTYPE html>
<html lang="en">
<head>
<meta charset="utf-8">
<title>Tallvex — Website Pages</title>
<link href="https://fonts.googleapis.com/css2?family=Manrope:wght@400;500;600;700&display=swap" rel="stylesheet">
<style>
:root{
  --board:#cfd0cc;
  --white:#ffffff;
  --ink:#10231a;
  --muted:#6f7a73;
  --green:#0f3d28;
  --green-2:#164d34;
  --deep:#0a2a1b;
  --leaf:#3b8a3e;
  --accent:#e2561e;
  --tint:#eef3e4;
  --cream:#f5f6f1;
  --line:#e3e6e1;
  --g-field:linear-gradient(160deg,#7aa35a,#3f6a2e 60%,#2a4a22);
  --g-brick:linear-gradient(160deg,#a9633c,#6e3a22 70%,#3d6b35);
  --g-eggs:linear-gradient(150deg,#e8b27a,#c97f45);
  --g-worker:linear-gradient(150deg,#d9782f,#7a4a2a 60%,#3e5e34);
  --g-lab:linear-gradient(150deg,#c9d7e2,#6f8ea8);
  --g-honey:linear-gradient(150deg,#e3a43c,#9b5a1c);
  --g-chips:linear-gradient(150deg,#e44a2c,#f0c24a 60%,#5c9a3c);
  --g-shelf:linear-gradient(150deg,#d9cfb7,#7e6a4a);
  --g-map:linear-gradient(150deg,#eef0f3,#d8dee6);
  --g-portrait:linear-gradient(150deg,#2d3a4e,#7b5a44);
}
*{box-sizing:border-box;margin:0;padding:0}
html,body{width:1200px;height:858px;overflow:hidden;background:var(--board);font-family:"Manrope",sans-serif;color:var(--ink)}
.board{position:relative;width:1200px;height:858px}
.page{position:absolute;width:532px;background:var(--white);overflow:hidden;display:flex;flex-direction:column;transform:scale(.25);transform-origin:0 0}
.nav{height:40px;flex:none;display:flex;align-items:center;gap:12px;padding:0 24px}
.logo{font-size:15px;font-weight:700;color:var(--green);letter-spacing:-.02em}
.logo.lt{color:#fff}
.links{margin-left:auto;font-size:5.6px;color:var(--muted);word-spacing:4px}
.navbtn{font-size:5px;color:#fff;background:var(--green);border-radius:8px;padding:3px 7px}
.sec{flex:none;position:relative;padding:24px 32px;overflow:hidden}
.hero{background:linear-gradient(180deg,var(--tint),#fff)}
.dark{background:var(--green);color:#fff;border-radius:50% 50% 0 0/32px 32px 0 0}
.dark.down{border-radius:0 0 50% 50%/0 0 32px 32px}
.dark.both{border-radius:50%/32px}
.cream{background:var(--cream)}
.h1{font-size:25px;font-weight:600;line-height:1.04;letter-spacing:-.03em}
.h2{font-size:19px;font-weight:600;line-height:1.08;letter-spacing:-.02em}
.h3{font-size:8.4px;font-weight:700;line-height:1.25}
.green-t{color:var(--leaf)}
.eb{font-size:5.4px;letter-spacing:.1em;text-transform:uppercase;color:var(--leaf);margin-bottom:6px;font-weight:600}
.dark .eb{color:#9fc98a}
.p{font-size:6.4px;line-height:1.45;color:var(--muted)}
.dark .p{color:#b8c9bd}
.btns{display:flex;gap:10px;margin-top:10px;align-items:center}
.btn{font-size:6px;font-weight:600;color:#fff;background:var(--accent);border-radius:12px;padding:4px 10px;white-space:nowrap}
.btn.ghost{background:none;color:var(--ink);padding:4px 0}
.dark .btn.ghost{color:#fff}
.ph{border-radius:8px;background:var(--g-field)}
.row{display:flex;gap:12px}
.col{flex:1;min-width:0}
.card{background:#fff;border-radius:8px;box-shadow:0 3px 10px rgba(16,35,26,.09);padding:10px}
.dark .card{background:var(--green-2);box-shadow:none}
.ic{width:12px;height:12px;border-radius:50%;background:var(--tint);border:1px solid var(--leaf);margin-bottom:6px}
.bul{font-size:6.2px;line-height:1.5;color:var(--muted);list-style:none}
.bul li::before{content:"•";color:var(--leaf);margin-right:4px}
.dark .bul{color:#b8c9bd}
.stats{display:flex;justify-content:space-between;margin-top:14px}
.stat b{display:block;font-size:19px;font-weight:600;letter-spacing:-.03em}
.stat sup{font-size:9px;color:var(--accent)}
.stat span{font-size:5.4px;color:var(--muted)}
.dark .stat span,.onimg .stat span{color:#b9c9be}
.onimg{color:#fff}
.onimg .p{color:#c9d6cd}
.cta{background:linear-gradient(120deg,var(--green),var(--green-2));color:#fff;border-radius:16px;padding:22px}
.cta .p{color:#b8c9bd}
.list{border-top:1px solid var(--line)}
.list div{border-bottom:1px solid var(--line);padding:7px 0;font-size:7px;font-weight:600;display:flex;justify-content:space-between}
.list small{display:block;font-size:5.2px;font-weight:400;color:var(--muted)}
.field{height:15px;border-bottom:1px solid #cdd3ce;font-size:5.4px;color:var(--muted);margin-bottom:7px}
.chip{font-size:5.4px;border:1px solid var(--line);border-radius:8px;padding:2px 7px}
.chip.on{background:var(--green);color:#fff;border-color:var(--green)}
.meta{font-size:5px;color:var(--leaf);margin-top:5px;text-transform:uppercase;letter-spacing:.08em}
.foot{flex:none;margin-top:auto;background:var(--deep);color:#c7d3cb;padding:28px 32px;display:flex;gap:16px}
.foot .fc{flex:1;font-size:5.6px;line-height:1.6}
.foot .fc:first-child{flex:1.6}
.foot i{font-style:normal;color:#fff;font-weight:600;display:block;margin-bottom:4px}
.fin{display:block;width:88px;height:12px;border-radius:8px;border:1px solid #3a5a48;margin-top:8px;font-size:5px;padding:2px 6px;color:#7f988a}
</style>
</head>
<body>
<div class="board">

<!-- HOME -->
<div class="page" style="left:23px;top:18px;height:3212px">
  <div class="nav"><span class="logo">Tallvex</span><span class="links">Home About Products Business Sustainability Careers News Contact</span><span class="navbtn">Contact us</span></div>
  <section class="sec hero" style="height:320px">
    <div class="row">
      <div class="col" style="padding-top:40px">
        <div class="eb">Premium food, made here</div>
        <div class="h1" style="font-size:29px">Integrated agriculture. <span class="green-t">Nourishing lives.</span></div>
        <p class="p" style="margin-top:12px">We farm, process, pack and distribute premium food across Nigeria, one standard from the first seedling to the shelf your customers buy from.</p>
        <div class="btns"><span class="btn">Explore products →</span><span class="btn ghost">About Tallvex</span></div>
      </div>
      <div class="col" style="display:grid;grid-template-columns:1fr 1fr;gap:8px;padding-top:24px">
        <div class="ph" role="img" aria-label="Egg trays on a packing line" style="grid-column:span 2;height:72px;background:var(--g-eggs)"></div>
        <div class="ph" role="img" aria-label="Company headquarters building" style="height:120px;background:var(--g-brick)"></div>
        <div class="ph" role="img" aria-label="Farm produce in crates" style="height:120px"></div>
      </div>
    </div>
  </section>
  <div class="sec" style="height:40px;padding:12px 32px"><p class="p" style="font-size:5.6px;letter-spacing:.06em">FARM · PROCESS · PACK · DISTRIBUTE · ACROSS 36 STATES · NAFDAC REGISTERED PRODUCTS</p></div>
  <section class="sec" style="height:220px">
    <div class="row">
      <div class="ph" role="img" aria-label="Headquarters building exterior" style="width:168px;height:152px;background:var(--g-brick)"></div>
      <div class="col">
        <div class="eb">Who we are</div>
        <div class="h2">A food company that owns its supply chain.</div>
        <p class="p" style="margin-top:8px">From breeder flocks to plantain farms, every stage runs under one roof and one set of checks. That is why our eggs, chips and honey taste the same in Lagos, Kano and Port Harcourt.</p>
        <div class="stats"><div class="stat"><b>1,000<sup>+</sup></b><span>Employees</span></div><div class="stat"><b>2,000<sup>+</sup></b><span>Outgrowers</span></div><div class="stat"><b>8</b><span>Sites</span></div></div>
      </div>
    </div>
  </section>
  <section class="sec" style="height:320px">
    <div class="row"><div class="col"><div class="eb">Products</div><div class="h2">Everyday food, held to a higher standard.</div></div><div class="col"><p class="p" style="margin-top:24px">Three lines, made to specification and sealed fresh for homes, hotels and trade buyers.</p><p class="meta">See all products →</p></div></div>
    <div class="row" style="margin-top:16px">
      <div class="col"><div class="ph" role="img" aria-label="Premium brown eggs in packs" style="height:110px;background:var(--g-eggs)"></div><div class="h3" style="margin-top:6px">Premium brown eggs</div><p class="p">Graded and sealed within a day of laying.</p></div>
      <div class="col"><div class="ph" role="img" aria-label="Plantain chips packs" style="height:110px;background:var(--g-chips)"></div><div class="h3" style="margin-top:6px">Crispy plantain chips</div><p class="p">Sliced from our own plantain, fried fresh.</p></div>
      <div class="col"><div class="ph" role="img" aria-label="Honey jars" style="height:110px;background:var(--g-honey)"></div><div class="h3" style="margin-top:6px">Pure honey</div><p class="p">Raw, filtered honey from partner hives.</p></div>
    </div>
  </section>
  <section class="sec dark" style="height:360px;padding-top:56px">
    <div class="eb">How we work</div>
    <div class="h2">Eight steps. One company accountable for all of them.</div>
    <div class="row" style="margin-top:20px">
      <div class="col"><div class="ph" role="img" aria-label="Plantain farm" style="height:88px"></div><div class="h3" style="margin-top:5px">Plantain farm</div><p class="p">Owned land and outgrowers.</p></div>
      <div class="col"><div class="ph" role="img" aria-label="Poultry house" style="height:88px;background:var(--g-shelf)"></div><div class="h3" style="margin-top:5px">Poultry production</div><p class="p">Climate-controlled houses.</p></div>
      <div class="col"><div class="ph" role="img" aria-label="Egg processing" style="height:88px;background:var(--g-eggs)"></div><div class="h3" style="margin-top:5px">Processing</div><p class="p">Food-grade plant lines.</p></div>
      <div class="col"><div class="ph" role="img" aria-label="Product packaging" style="height:88px;background:var(--g-chips)"></div><div class="h3" style="margin-top:5px">Packaging</div><p class="p">Sealed and batch coded.</p></div>
    </div>
    <p class="meta" style="color:#9fc98a;margin-top:12px">See the value chain →</p>
  </section>
  <section class="sec onimg" style="height:248px;background:linear-gradient(120deg,#0f3d28 40%,#6b4a2a);border-radius:0 0 50% 50%/0 0 32px 32px" role="img" aria-label="Brown eggs close up behind text">
    <div class="eb" style="color:#9fc98a;margin-top:24px">Traceability</div>
    <div class="h2">Quality you can trace, in every single pack.</div>
    <p class="p" style="margin-top:6px">Every batch carries a code back to its house, flock and laying date.</p>
    <div class="stats"><div class="stat"><b>8</b><span>Quality checks</span></div><div class="stat"><b>AA</b><span>Egg grade</span></div><div class="stat"><b>36<sup>h</sup></b><span>Farm to shelf</span></div><div class="stat"><b>Zero</b><span>Growth hormones</span></div></div>
  </section>
  <section class="sec" style="height:320px;padding-top:48px">
    <div class="row">
      <div class="col"><div class="eb">Quality</div><div class="h2">Claims we can show you the paperwork for.</div><p class="p" style="margin-top:8px">Lab testing, audit trails and batch records, open to buyers on request. We would rather show you a file than make a promise.</p>
        <ul class="bul" style="margin-top:8px"><li>In-house laboratory testing on every batch</li><li>Documented feed and vaccination records</li><li>Cold storage logged every hour</li><li>Recall drill run twice a year</li></ul><p class="meta">Our quality system →</p></div>
      <div class="col" style="display:grid;grid-template-columns:1fr 1fr;gap:8px">
        <div class="ph" role="img" aria-label="Lab technician testing samples" style="grid-column:span 2;height:80px;background:var(--g-lab)"></div>
        <div class="ph" role="img" aria-label="Produce sorting" style="height:72px;background:var(--g-worker)"></div>
        <div class="ph" role="img" aria-label="Egg trays" style="height:72px;background:var(--g-eggs)"></div>
      </div>
    </div>
  </section>
  <section class="sec" style="height:640px">
    <div class="row"><div class="col"><div class="eb">Sustainability</div><div class="h2">Responsible practice, made visible.</div></div><div class="col"><p class="p" style="margin-top:24px">We report on what we do, not what we plan to do. Our ESG figures are published every year.</p><p class="meta">Read the ESG approach →</p></div></div>
    <div class="ph" role="img" aria-label="Aerial view of green farmland" style="height:160px;margin-top:16px"></div>
    <div class="row" style="margin-top:16px">
      <div class="col card"><div class="ic"></div><div class="h3">Environmental</div><p class="p">Manure turned to compost, water reused and solar power at two sites.</p></div>
      <div class="col card"><div class="ic"></div><div class="h3">Social</div><p class="p">Local jobs, farmer training and fair pay across our communities.</p></div>
      <div class="col card"><div class="ic"></div><div class="h3">Governance</div><p class="p">Audited accounts, board oversight and clear public reporting.</p></div>
    </div>
    <div class="stats" style="margin-top:64px"><div class="stat"><b>1,000<sup>+</sup></b><span>Direct jobs</span></div><div class="stat"><b>2,000<sup>+</sup></b><span>Farmers supported</span></div><div class="stat"><b>500<sup>+</sup></b><span>Hectares farmed</span></div><div class="stat"><b>300<sup>+</sup></b><span>Trade partners</span></div></div>
  </section>
  <section class="sec" style="height:340px;padding-top:40px">
    <div class="row"><div class="col"><div class="eb">Newsroom</div><div class="h2">What is happening at Tallvex</div></div><p class="meta" style="margin-top:28px">All news →</p></div>
    <div class="row" style="margin-top:16px">
      <div class="col"><div class="ph" role="img" aria-label="Processing plant interior" style="height:88px;background:var(--g-lab)"></div><div class="h3" style="margin-top:6px">New processing line commissioned</div><p class="p">Chip output doubles at our main plant.</p><p class="meta">Read →</p></div>
      <div class="col"><div class="ph" role="img" aria-label="Farmers in a plantain field" style="height:88px"></div><div class="h3" style="margin-top:6px">Outgrower programme reaches 2,000</div><p class="p">Farmers trained across three states.</p><p class="meta">Read →</p></div>
      <div class="col"><div class="ph" role="img" aria-label="Retail shelves" style="height:88px;background:var(--g-shelf)"></div><div class="h3" style="margin-top:6px">Eggs now in national retail</div><p class="p">Premium packs arrive on major shelves.</p><p class="meta">Read →</p></div>
    </div>
  </section>
  <section class="sec" style="height:200px">
    <div class="cta" style="padding:28px"><div class="row"><div class="col"><div class="eb" style="color:#9fc98a">Trade &amp; institutional supply</div><div class="h2" style="font-size:16px">Stocking Tallvex, or sourcing at volume?</div><p class="p" style="margin-top:6px">We supply supermarkets, hotels, caterers and distributors with agreed specifications and scheduled delivery.</p></div><div class="btns" style="flex-direction:column;align-items:flex-start"><span class="btn">Talk to our trade team →</span><span class="btn ghost" style="color:#fff">Download catalogue</span></div></div></div>
  </section>
  <footer class="foot"><div class="fc"><b class="logo lt">Tallvex</b><br>Morrowdale Farms Limited. Premium food grown, made and delivered in Nigeria.<span class="fin">Your email →</span></div><div class="fc"><i>Company</i>About<br>Our business<br>Sustainability<br>Careers<br>News</div><div class="fc"><i>Products</i>Premium eggs<br>Plantain chips<br>Pure honey<br>Trade supply</div><div class="fc"><i>Visit</i>Harbour Row, Lagos<br>+234 700 000 0000<br>hello@tallvex.example</div></footer>
</div>

<!-- SUSTAINABILITY -->
<div class="page" style="left:169px;top:18px;height:1864px">
  <div class="nav"><span class="logo">Tallvex</span><span class="links">Home About Products Business Sustainability Careers News Contact</span><span class="navbtn">Contact us</span></div>
  <section class="sec hero" style="height:240px">
    <div class="row"><div class="col" style="padding-top:32px"><div class="eb">Sustainability</div><div class="h1">Responsible practice, made visible.</div><p class="p" style="margin-top:8px">Sustainability at Tallvex is measured in the things that leave the farm: soil, water, waste, jobs and the communities around our sites.</p></div>
    <div class="ph" role="img" aria-label="Aerial view of farmland with a winding road" style="width:200px;height:160px"></div></div>
  </section>
  <section class="sec dark down" style="height:220px;padding-top:48px;border-radius:0 0 50% 50%/0 0 40px 40px">
    <div class="eb">Our commitment</div>
    <div class="h2" style="width:340px">We measure what we leave behind, not just what we take out.</div>
    <p class="p" style="margin-top:8px;width:340px">Every site reports on energy, water, waste and people each quarter, and the numbers are reviewed by the board.</p>
  </section>
  <section class="sec" style="height:400px;padding-top:48px">
    <div class="row"><div class="col"><div class="eb">Framework</div><div class="h2">Environmental. Social. Governance.</div></div><div class="col"><p class="p" style="margin-top:40px">Three areas, each with targets we can be held to and results we publish.</p></div></div>
    <div class="row" style="margin-top:24px">
      <div class="col card"><div class="ic"></div><div class="h3">Environmental</div><ul class="bul" style="margin-top:4px"><li>Sustainable farming practices</li><li>Manure turned to compost</li><li>Efficient use of water</li><li>Solar power at two sites</li></ul></div>
      <div class="col card"><div class="ic"></div><div class="h3">Social</div><ul class="bul" style="margin-top:4px"><li>Jobs created in rural areas</li><li>Support for local farmers</li><li>Youth employment</li><li>Health and safety first</li></ul></div>
      <div class="col card"><div class="ic"></div><div class="h3">Governance</div><ul class="bul" style="margin-top:4px"><li>Ethical business practice</li><li>Transparent reporting</li><li>Compliance with regulation</li><li>Strong board oversight</li></ul></div>
    </div>
  </section>
  <section class="sec dark both" style="height:280px;padding-top:56px">
    <div class="row"><div class="col"><div class="eb">Impact</div><div class="h2">Real impact, lasting change.</div></div><div class="col"><p class="p" style="margin-top:16px">Results we track across our farms, plants and the communities around them.</p></div></div>
    <div class="stats" style="margin-top:24px"><div class="stat"><b>1,000<sup>+</sup></b><span>Direct jobs</span></div><div class="stat"><b>2,000<sup>+</sup></b><span>Farmers supported</span></div><div class="stat"><b>500<sup>+</sup></b><span>Hectares farmed</span></div><div class="stat"><b>300<sup>+</sup></b><span>Trade partners</span></div></div>
  </section>
  <section class="sec" style="height:344px;padding-top:40px">
    <div class="row">
      <div class="ph" role="img" aria-label="Smiling farmer holding produce" style="width:160px;height:176px;background:var(--g-worker)"></div>
      <div class="col"><div class="eb">Community</div><div class="h2" style="font-size:15px">When we uplift our communities, we cultivate a better future for all.</div>
      <ul class="bul" style="margin-top:8px"><li><b>Employment generation</b> — hundreds of jobs near our farms</li><li><b>Farmer support</b> — inputs, training and fair offtake</li><li><b>Youth empowerment</b> — apprenticeships in farming and food</li><li><b>Women in agriculture</b> — support for women-led farms</li></ul></div>
    </div>
    <div class="row" style="margin-top:12px">
      <div class="col ph" role="img" aria-label="Farm workers in the field" style="height:56px"></div>
      <div class="col ph" role="img" aria-label="Beekeeping hives" style="height:56px;background:var(--g-honey)"></div>
      <div class="col ph" role="img" aria-label="Farmers at a training day" style="height:56px;background:var(--g-worker)"></div>
    </div>
  </section>
  <section class="sec" style="height:160px;text-align:center;padding-top:40px">
    <div class="eb">Our belief</div>
    <div class="h3" style="font-size:12px">We believe sustainable actions today create lasting value for future generations.</div>
    <div class="btns" style="justify-content:center"><span class="btn" style="background:var(--green)">Read the report →</span><span class="btn ghost">Partner with us</span></div>
  </section>
  <footer class="foot"><div class="fc"><b class="logo lt">Tallvex</b><br>Morrowdale Farms Limited. Premium food grown, made and delivered in Nigeria.<span class="fin">Your email →</span></div><div class="fc"><i>Company</i>About<br>Our business<br>Sustainability<br>Careers</div><div class="fc"><i>Products</i>Premium eggs<br>Plantain chips<br>Pure honey</div><div class="fc"><i>Visit</i>Harbour Row, Lagos<br>+234 700 000 0000<br>hello@tallvex.example</div></footer>
</div>

<!-- INVESTORS -->
<div class="page" style="left:315px;top:18px;height:1684px">
  <div class="nav"><span class="logo">Tallvex</span><span class="links">Home About Products Business Sustainability Careers News Contact</span><span class="navbtn">Contact us</span></div>
  <section class="sec hero" style="height:260px">
    <div class="row"><div class="col" style="padding-top:32px"><div class="eb">Investors</div><div class="h1" style="font-size:22px">An integrated food business, built for the next decade of African demand.</div><p class="p" style="margin-top:8px">Scale, control and discipline across the food chain, with capacity already in place.</p><div class="btns"><span class="btn">Request investor deck →</span><span class="btn ghost">Download profile</span></div></div>
    <div class="ph" role="img" aria-label="Headquarters building exterior" style="width:200px;height:176px;background:var(--g-brick)"></div></div>
  </section>
  <section class="sec" style="height:164px">
    <div class="stats" style="margin-top:24px"><div class="stat"><b>3</b><span>Consumer product lines</span></div><div class="stat"><b>6</b><span>Operating divisions</span></div><div class="stat"><b>8</b><span>Production sites</span></div><div class="stat"><b>1,000<sup>+</sup></b><span>Full-time staff</span></div></div>
  </section>
  <section class="sec" style="height:300px">
    <div class="row"><div class="col"><div class="eb">The opportunity</div><div class="h2">Why this business, in this market.</div>
    <ul class="bul" style="margin-top:10px"><li><b>Integrated production</b> — we control cost and quality at each stage</li><li><b>Staple demand, branded delivery</b> — everyday food sold as a premium brand</li><li><b>Risk built into the model</b> — own inputs reduce price shocks</li><li><b>Capacity already in place</b> — plants running below full load</li><li><b>Structured for growth</b> — clear governance and reporting</li></ul></div>
    <div class="ph" role="img" aria-label="Worker inspecting a processing line" style="width:184px;height:224px;background:var(--g-lab)"></div></div>
  </section>
  <section class="sec dark both" style="height:300px;padding-top:56px">
    <div class="row"><div class="col"><div class="h2">A future of endless possibilities.</div></div><div class="col"><p class="p" style="margin-top:16px">Where the group is headed over the next five years.</p></div></div>
    <div class="row" style="margin-top:20px">
      <div class="col card"><div class="ic"></div><div class="h3">Expanding capacity</div><p class="p">New layer houses and a second chip line.</p></div>
      <div class="col card"><div class="ic"></div><div class="h3">Product innovation</div><p class="p">New snack formats and flavours.</p></div>
      <div class="col card"><div class="ic"></div><div class="h3">Technology driven</div><p class="p">Farm data and smart logistics.</p></div>
      <div class="col card"><div class="ic"></div><div class="h3">Export focus</div><p class="p">Regional markets in West Africa.</p></div>
    </div>
  </section>
  <section class="sec" style="height:260px;padding-top:40px">
    <div class="row">
      <div class="col"><div class="h3" style="font-size:11px">Where the next naira of capital goes.</div><div class="list" style="margin-top:10px"><div>Layer capacity<small>+40% house space</small></div><div>Processing lines<small>Chips and honey</small></div><div>Cold chain fleet<small>Regional hubs</small></div><div>Export readiness<small>Certification</small></div></div></div>
      <div class="col"><div class="h3" style="font-size:11px">How the business is overseen.</div><ul class="bul" style="margin-top:10px"><li>Independent non-executive board</li><li>Audit and risk committee</li><li>Quarterly management reporting</li><li>External annual audit</li></ul><div class="card" style="margin-top:10px"><div class="h3">Investor relations</div><p class="p">Speak with our finance team.</p><div class="btns"><span class="btn" style="background:var(--green)">Get in touch</span></div></div></div>
    </div>
  </section>
  <section class="sec" style="height:180px">
    <div class="cta"><div class="row"><div class="col"><div class="eb" style="color:#9fc98a">Partnership</div><div class="h2" style="font-size:15px">Building today. Growing tomorrow. Feeding the world.</div></div><div class="btns"><span class="btn">Arrange a conversation →</span></div></div></div>
  </section>
  <footer class="foot"><div class="fc"><b class="logo lt">Tallvex</b><br>Morrowdale Farms Limited. Premium food grown, made and delivered in Nigeria.<span class="fin">Your email →</span></div><div class="fc"><i>Company</i>About<br>Our business<br>Sustainability<br>Careers</div><div class="fc"><i>Products</i>Premium eggs<br>Plantain chips<br>Pure honey</div><div class="fc"><i>Visit</i>Harbour Row, Lagos<br>+234 700 000 0000<br>hello@tallvex.example</div></footer>
</div>

<!-- CONTACT -->
<div class="page" style="left:315px;top:453px;height:1408px">
  <div class="nav"><span class="logo">Tallvex</span><span class="links">Home About Products Business Sustainability Careers News Contact</span><span class="navbtn">Contact us</span></div>
  <section class="sec hero" style="height:220px">
    <div class="row"><div class="col" style="padding-top:48px"><div class="eb">Contact</div><div class="h1">Let's talk.</div><p class="p" style="margin-top:8px">Whether you want to stock our products, supply us or partner with us, we reply within one working day.</p></div>
    <div class="ph" role="img" aria-label="Headquarters building exterior" style="width:200px;height:160px;background:var(--g-brick)"></div></div>
  </section>
  <section class="sec" style="height:160px">
    <div class="row">
      <div class="col card"><div class="ic"></div><div class="h3">General enquiries</div><p class="p">Questions about the company.</p><p class="meta">hello@tallvex.example</p></div>
      <div class="col card"><div class="ic"></div><div class="h3">Trade &amp; distribution</div><p class="p">Bulk and retail supply.</p><p class="meta">Talk to sales →</p></div>
      <div class="col card"><div class="ic"></div><div class="h3">Careers</div><p class="p">Roles and applications.</p><p class="meta">Open roles →</p></div>
      <div class="col card"><div class="ic"></div><div class="h3">Media</div><p class="p">Press and interviews.</p><p class="meta">Press office →</p></div>
    </div>
  </section>
  <section class="sec" style="height:380px;padding-top:40px">
    <div class="row">
      <div class="col" style="flex:1.6"><div class="eb">Enquiry form</div><div class="h2" style="font-size:16px">Tell us what you need.</div><p class="p" style="margin:8px 0 12px">We route each request to the right team, so a few details help.</p>
        <div class="row"><div class="col field">Full name</div><div class="col field">Company</div></div>
        <div class="row"><div class="col field">Email address</div><div class="col field">Phone number</div></div>
        <div class="field">Enquiry type — select one</div><div class="field" style="height:48px">Your message</div>
        <p class="p" style="font-size:5.4px">☐ I agree to be contacted about my enquiry.</p>
        <div class="btns"><span class="btn">Send message →</span></div></div>
      <div class="col"><div class="card"><div class="h3">Head office</div><p class="p">Harbour Row, Lagos<br>+234 700 000 0000<br>hello@tallvex.example<br>Mon–Fri, 8am–5pm</p></div><div class="card" style="margin-top:10px"><div class="h3">Our sites</div><p class="p">Poultry farm · Processing plant · Plantation</p></div><div class="card" style="margin-top:10px"><div class="h3">Follow Tallvex</div><p class="p">News, recipes and updates.</p></div></div>
    </div>
  </section>
  <section class="sec" style="height:420px">
    <div class="row"><div class="col"><div class="eb">Visit</div><div class="h2">Harbour Row, Lagos, Nigeria.</div></div><div class="col"><p class="p" style="margin-top:16px">Our head office is minutes from the airport. Visitors please book ahead.</p></div></div>
    <div class="ph" role="img" aria-label="Street map around the head office" style="height:248px;margin-top:16px;background:var(--g-map)"></div>
  </section>
  <footer class="foot"><div class="fc"><b class="logo lt">Tallvex</b><br>Morrowdale Farms Limited. Premium food grown, made and delivered in Nigeria.<span class="fin">Your email →</span></div><div class="fc"><i>Company</i>About<br>Our business<br>Sustainability<br>Careers</div><div class="fc"><i>Products</i>Premium eggs<br>Plantain chips<br>Pure honey</div><div class="fc"><i>Visit</i>Harbour Row, Lagos<br>+234 700 000 0000<br>hello@tallvex.example</div></footer>
</div>

<!-- NEWSROOM -->
<div class="page" style="left:461px;top:18px;height:1948px">
  <div class="nav"><span class="logo">Tallvex</span><span class="links">Home About Products Business Sustainability Careers News Contact</span><span class="navbtn">Contact us</span></div>
  <section class="sec hero" style="height:240px">
    <div class="row"><div class="col" style="padding-top:56px"><div class="eb">News</div><div class="h1">Newsroom</div><p class="p" style="margin-top:8px">Company news, press releases, photography and stories from our farms, plants and people.</p></div>
    <div style="width:184px;display:grid;gap:8px"><div class="ph" role="img" aria-label="Farm workers in a field" style="height:72px;background:var(--g-worker)"></div><div class="ph" role="img" aria-label="Plantain bunches" style="height:56px"></div></div></div>
  </section>
  <section class="sec" style="height:648px">
    <div class="row" style="gap:6px"><span class="chip on">All</span><span class="chip">Company news</span><span class="chip">Press releases</span><span class="chip">Community</span><span class="chip">Events</span></div>
    <div style="display:grid;grid-template-columns:repeat(3,1fr);gap:12px;margin-top:16px">
      <div><div class="ph" role="img" aria-label="Processing plant" style="height:64px;background:var(--g-lab)"></div><p class="meta">Company · May</p><div class="h3">Second processing line opens</div><p class="p">Chip output doubles at the plant.</p></div>
      <div><div class="ph" role="img" aria-label="Retail shelves" style="height:64px;background:var(--g-shelf)"></div><p class="meta">Press · April</p><div class="h3">Eggs on national retail shelves</div><p class="p">Premium packs go nationwide.</p></div>
      <div><div class="ph" role="img" aria-label="Plantain farm" style="height:64px"></div><p class="meta">Community · April</p><div class="h3">Outgrowers reach 2,000</div><p class="p">Training across three states.</p></div>
      <div><div class="ph" role="img" aria-label="Plantain chips packs" style="height:64px;background:var(--g-chips)"></div><p class="meta">Products · March</p><div class="h3">New chip flavours launch</div><p class="p">Spicy and sweet now in store.</p></div>
      <div><div class="ph" role="img" aria-label="Beehives" style="height:64px;background:var(--g-honey)"></div><p class="meta">Community · March</p><div class="h3">Beekeeper training expands</div><p class="p">New hives with partner farmers.</p></div>
      <div><div class="ph" role="img" aria-label="Team meeting" style="height:64px;background:var(--g-worker)"></div><p class="meta">Events · February</p><div class="h3">Tallvex joins food forum</div><p class="p">Speaking on food security.</p></div>
      <div><div class="ph" role="img" aria-label="Market stall" style="height:64px;background:var(--g-eggs)"></div><p class="meta">Company · January</p><div class="h3">Layer capacity completed</div><p class="p">New houses now in lay.</p></div>
      <div><div class="ph" role="img" aria-label="Field visit" style="height:64px"></div><p class="meta">Community · January</p><div class="h3">Field day for farmers</div><p class="p">Best practice shared on site.</p></div>
    </div>
  </section>
  <section class="sec" style="height:480px;background:linear-gradient(180deg,#fff,var(--cream))">
    <div class="row"><div class="col"><div class="eb">Gallery</div><div class="h2">Inside the operation.</div></div><div class="col"><p class="p" style="margin-top:24px">Photography from our farms, plants and fleet, free for editorial use with credit.</p></div></div>
    <div style="display:grid;grid-template-columns:repeat(3,1fr);gap:8px;margin-top:16px">
      <div class="ph" role="img" aria-label="Egg collection" style="height:88px;background:var(--g-eggs)"></div>
      <div class="ph" role="img" aria-label="Delivery van" style="height:88px;background:var(--g-lab)"></div>
      <div class="ph" role="img" aria-label="Honey pouring" style="height:88px;background:var(--g-honey)"></div>
      <div class="ph" role="img" aria-label="Farm worker" style="height:88px;background:var(--g-worker)"></div>
      <div class="ph" role="img" aria-label="Plantain field" style="height:88px"></div>
      <div class="ph" role="img" aria-label="Storage room" style="height:88px;background:var(--g-shelf)"></div>
      <div class="ph" role="img" aria-label="Packed chips" style="height:72px;background:var(--g-chips)"></div>
      <div class="ph" role="img" aria-label="Harvest crates" style="height:72px"></div>
    </div>
  </section>
  <section class="sec" style="height:220px;padding-top:40px">
    <div class="row"><div class="col"><div class="eb">Film</div><div class="h3" style="font-size:12px">From our farm to your table</div><p class="p" style="margin-top:8px">A short film following a pack from field, through processing and quality checks, to the shelf.</p><div class="btns"><span class="btn" style="background:var(--green)">Watch film ▸</span></div></div><div class="ph" role="img" aria-label="Worker holding plantain chips" style="width:200px;height:120px;background:var(--g-worker)"></div></div>
  </section>
  <section class="sec" style="height:140px">
    <div class="cta" style="padding:20px"><div class="row"><div class="col"><div class="eb" style="color:#9fc98a">Media enquiries</div><div class="h3" style="font-size:12px">Working on a story?</div><p class="p">Our media team can arrange interviews, images and site visits.</p></div><div class="btns"><span class="btn">Contact press →</span></div></div></div>
  </section>
  <footer class="foot"><div class="fc"><b class="logo lt">Tallvex</b><br>Morrowdale Farms Limited. Premium food grown, made and delivered in Nigeria.<span class="fin">Your email →</span></div><div class="fc"><i>Company</i>About<br>Our business<br>Sustainability<br>Careers</div><div class="fc"><i>Products</i>Premium eggs<br>Plantain chips<br>Pure honey</div><div class="fc"><i>Visit</i>Harbour Row, Lagos<br>+234 700 000 0000<br>hello@tallvex.example</div></footer>
</div>

<!-- CAREERS -->
<div class="page" style="left:608px;top:18px;height:1452px">
  <div class="nav"><span class="logo">Tallvex</span><span class="links">Home About Products Business Sustainability Careers News Contact</span><span class="navbtn">Contact us</span></div>
  <section class="sec hero" style="height:260px">
    <div class="row"><div class="col" style="padding-top:32px"><div class="eb">Careers</div><div class="h1" style="font-size:22px">Work where the standard is the whole point.</div><p class="p" style="margin-top:8px">Join the teams that farm, make and move food the country relies on, every single day.</p><div class="btns"><span class="btn">See open roles →</span><span class="btn ghost">Send application</span></div></div>
    <div class="ph" role="img" aria-label="Lab technicians at microscopes" style="width:200px;height:152px;background:var(--g-lab)"></div></div>
  </section>
  <section class="sec" style="height:332px;padding-top:40px">
    <div class="row">
      <div class="ph" role="img" aria-label="Worker in orange overalls with plantain" style="width:184px;height:224px;background:var(--g-worker)"></div>
      <div class="col"><div class="eb">Why join</div><div class="h3" style="font-size:12px">Real responsibility, early.</div><p class="p" style="margin-top:4px">You will own real work from your first month, with people around you who know the job.</p>
        <div style="display:grid;grid-template-columns:1fr 1fr;gap:8px;margin-top:10px">
          <div class="card"><div class="ic"></div><div class="h3">Learn the whole chain</div><p class="p">Rotate from farm to fleet.</p></div>
          <div class="card"><div class="ic"></div><div class="h3">Training that counts</div><p class="p">Certified skills, paid for.</p></div>
          <div class="card"><div class="ic"></div><div class="h3">Safety first, always</div><p class="p">Gear, drills and checks.</p></div>
          <div class="card"><div class="ic"></div><div class="h3">Grow with us</div><p class="p">Most leads promoted within.</p></div>
        </div></div>
    </div>
  </section>
  <section class="sec cream" style="height:340px;padding-top:48px">
    <div class="row"><div class="col"><div class="eb">Vacancies</div><div class="h2">Open roles</div></div><div class="col"><p class="p" style="margin-top:20px">Apply online. We reply to every application within two weeks.</p></div></div>
    <div class="list" style="margin-top:16px"><div><span>Quality Assurance Officer<small>Processing plant · Full time</small></span><span>›</span></div><div><span>Poultry Farm Supervisor<small>Layer farm · Full time</small></span><span>›</span></div><div><span>Sales Representative, Trade<small>Lagos · Full time</small></span><span>›</span></div><div><span>Production Machine Operator<small>Processing plant · Shift</small></span><span>›</span></div><div><span>Logistics &amp; Fleet Coordinator<small>Head office · Full time</small></span><span>›</span></div></div>
  </section>
  <section class="sec" style="height:320px;padding-top:48px">
    <div class="row"><div class="col"><div class="eb">Apply</div><div class="h3" style="font-size:12px">Send us your application.</div><p class="p" style="margin-top:4px">No role listed that fits? Send your CV anyway and we will keep it on file.</p><div class="card" style="margin-top:10px"><div class="h3">Prefer email?</div><p class="p">hello@tallvex.example</p></div></div>
    <div class="col" style="flex:1.4"><div class="row"><div class="col field">Full name</div><div class="col field">Email</div></div><div class="row"><div class="col field">Phone</div><div class="col field">Role applied for</div></div><div class="field">Upload CV (PDF)</div><div class="field" style="height:36px">Short cover note</div><div class="btns"><span class="btn">Submit application →</span></div></div></div>
  </section>
  <footer class="foot"><div class="fc"><b class="logo lt">Tallvex</b><br>Morrowdale Farms Limited. Premium food grown, made and delivered in Nigeria.<span class="fin">Your email →</span></div><div class="fc"><i>Company</i>About<br>Our business<br>Sustainability<br>Careers</div><div class="fc"><i>Products</i>Premium eggs<br>Plantain chips<br>Pure honey</div><div class="fc"><i>Visit</i>Harbour Row, Lagos<br>+234 700 000 0000<br>hello@tallvex.example</div></footer>
</div>

<!-- OUR BUSINESS -->
<div class="page" style="left:754px;top:18px;height:2836px">
  <div class="nav"><span class="logo">Tallvex</span><span class="links">Home About Products Business Sustainability Careers News Contact</span><span class="navbtn">Contact us</span></div>
  <section class="sec hero" style="height:240px">
    <div class="row"><div class="col" style="padding-top:48px"><div class="eb">Our business</div><div class="h1" style="font-size:22px">Six divisions, run as one operation.</div><p class="p" style="margin-top:8px">Farming, processing, packaging and distribution. Each division feeds the next, under one standard.</p></div>
    <div class="ph" role="img" aria-label="Worker holding plantain bunch" style="width:200px;height:160px;background:var(--g-worker)"></div></div>
  </section>
  <section class="sec" style="height:320px;padding-top:32px">
    <div style="display:grid;grid-template-columns:repeat(3,1fr);gap:12px">
      <div class="card"><div class="ic"></div><div class="h3">Poultry</div><p class="p">Layer and breeder flocks in climate-controlled houses.</p></div>
      <div class="card"><div class="ic"></div><div class="h3">Plantain farming</div><p class="p">Owned estates and outgrower farms under contract.</p></div>
      <div class="card"><div class="ic"></div><div class="h3">Food processing</div><p class="p">Chips, honey and egg grading to food-grade rules.</p></div>
      <div class="card"><div class="ic"></div><div class="h3">Distribution</div><p class="p">Own fleet and regional hubs serving all states.</p></div>
      <div class="card"><div class="ic"></div><div class="h3">Quality assurance</div><p class="p">In-house laboratory testing every batch.</p></div>
      <div class="card"><div class="ic"></div><div class="h3">Research &amp; innovation</div><p class="p">New products and better farm yields.</p></div>
    </div>
  </section>
  <section class="sec dark" style="height:340px;padding-top:64px;border-radius:50% 50% 0 0/40px 40px 0 0">
    <div class="eb">Value chain</div><div class="h2">From our farm to your table, step by step.</div>
    <div class="row" style="margin-top:20px">
      <div class="col"><div class="ph" role="img" aria-label="Plantain farm" style="height:72px"></div><div class="h3" style="margin-top:4px">Plantain farm</div><p class="p">Grown on our land.</p></div>
      <div class="col"><div class="ph" role="img" aria-label="Poultry house" style="height:72px;background:var(--g-shelf)"></div><div class="h3" style="margin-top:4px">Poultry</div><p class="p">Healthy flocks.</p></div>
      <div class="col"><div class="ph" role="img" aria-label="Processing line" style="height:72px;background:var(--g-lab)"></div><div class="h3" style="margin-top:4px">Processing</div><p class="p">Clean lines.</p></div>
      <div class="col"><div class="ph" role="img" aria-label="Egg sorting" style="height:72px;background:var(--g-eggs)"></div><div class="h3" style="margin-top:4px">Sorting</div><p class="p">Graded daily.</p></div>
      <div class="col"><div class="ph" role="img" aria-label="Packaging" style="height:72px;background:var(--g-chips)"></div><div class="h3" style="margin-top:4px">Packaging</div><p class="p">Sealed and coded.</p></div>
    </div>
  </section>
  <section class="sec onimg" style="height:260px;background:linear-gradient(120deg,#0c3322 45%,#3c4a40);border-radius:0 0 50% 50%/0 0 40px 40px" role="img" aria-label="Processing hall behind text">
    <div class="eb" style="color:#9fc98a;margin-top:8px">Operations</div>
    <div class="h2" style="width:320px">Built to run to standard every day, not just on a good day.</div>
    <p class="p" style="margin-top:6px;width:320px">Automated, monitored and documented across every division.</p>
    <div class="stats"><div class="stat"><b>6</b><span>Divisions</span></div><div class="stat"><b>Daily</b><span>Quality checks</span></div><div class="stat"><b>100%</b><span>Traceable batches</span></div></div>
  </section>
  <section class="sec" style="height:280px;padding-top:40px">
    <div class="row"><div class="col"><div class="eb">Division one</div><div class="h3" style="font-size:12px">Poultry operations</div><p class="p" style="margin-top:6px">Our layer farm runs on strict biosecurity, with feed milled in-house and every house logged daily.</p><ul class="bul" style="margin-top:6px"><li>Climate-controlled houses</li><li>Feed made in-house</li><li>Vet checks every week</li><li>Eggs graded and packed daily</li></ul></div><div class="ph" role="img" aria-label="Hens in a poultry house" style="width:200px;height:120px;background:var(--g-shelf)"></div></div>
  </section>
  <section class="sec" style="height:320px">
    <div class="row"><div style="width:200px;display:grid;gap:8px"><div class="ph" role="img" aria-label="Worker with plantain bunch" style="height:96px;background:var(--g-worker)"></div><div class="ph" role="img" aria-label="Sliced plantain chips" style="height:96px;background:var(--g-honey)"></div></div>
    <div class="col"><div class="eb">Division two</div><div class="h3" style="font-size:12px">Food processing</div><p class="p" style="margin-top:6px">Our plant slices, fries and seals plantain chips, and filters and bottles honey under food-grade conditions with trained operators on each line.</p><ul class="bul" style="margin-top:6px"><li>Sorted by size and ripeness</li><li>Fried in controlled batches</li><li>Nitrogen-flushed packs</li><li>Metal detection on every line</li></ul></div></div>
  </section>
  <section class="sec" style="height:320px;padding-top:48px">
    <div class="row"><div class="col"><div class="eb">Quality</div><div class="h3" style="font-size:12px">A claim on the pack is a record in the file.</div><div class="ph" role="img" aria-label="Lab technician with samples" style="height:88px;margin-top:12px;background:var(--g-lab)"></div></div>
    <div class="col"><p class="p">Quality is not a final check, it is a sequence of steps.</p><ul class="bul" style="margin-top:6px"><li><b>Incoming material</b> — feed, oil and packaging tested</li><li><b>In-process</b> — temperature and moisture logged</li><li><b>Laboratory</b> — microbial and shelf-life tests</li><li><b>Release</b> — signed off batch by batch</li><li><b>Traceability</b> — code links pack to source</li></ul></div></div>
  </section>
  <section class="sec" style="height:340px;padding-top:40px">
    <div class="row"><div class="col"><div class="eb">Division three</div><div class="h3" style="font-size:12px">Distribution and route to market</div><p class="p" style="margin-top:6px">Own fleet, regional hubs and trade partners get product to shelves fast, with cold chain where it matters.</p><div class="stats"><div class="stat"><b>36<sup>h</sup></b><span>Farm to shelf</span></div><div class="stat"><b>Daily</b><span>Delivery runs</span></div></div></div>
    <div style="width:192px;display:grid;gap:8px"><div class="ph" role="img" aria-label="Delivery vans" style="height:104px;background:var(--g-lab)"></div><div class="ph" role="img" aria-label="Supermarket aisle" style="height:104px;background:var(--g-shelf)"></div></div></div>
  </section>
  <section class="sec" style="height:180px">
    <div class="cta"><div class="row"><div class="col"><div class="eb" style="color:#9fc98a">Work with us</div><div class="h3" style="font-size:12px">Supplying us, buying from us, or building with us?</div><p class="p">Tell us what you need and the right team will follow up.</p></div><div class="btns"><span class="btn">Contact us →</span></div></div></div>
  </section>
  <footer class="foot"><div class="fc"><b class="logo lt">Tallvex</b><br>Morrowdale Farms Limited. Premium food grown, made and delivered in Nigeria.<span class="fin">Your email →</span></div><div class="fc"><i>Company</i>About<br>Our business<br>Sustainability<br>Careers</div><div class="fc"><i>Products</i>Premium eggs<br>Plantain chips<br>Pure honey</div><div class="fc"><i>Visit</i>Harbour Row, Lagos<br>+234 700 000 0000<br>hello@tallvex.example</div></footer>
</div>

<!-- ABOUT -->
<div class="page" style="left:900px;top:18px;height:2532px">
  <div class="nav"><span class="logo">Tallvex</span><span class="links">Home About Products Business Sustainability Careers News Contact</span><span class="navbtn">Contact us</span></div>
  <section class="sec hero" style="height:260px">
    <div class="row"><div class="col" style="padding-top:32px"><div class="eb">About</div><div class="h1" style="font-size:21px">We grew into the supply chain instead of buying our way through it.</div><p class="p" style="margin-top:8px">From one farm to a national food company, built one step at a time.</p></div>
    <div class="ph" role="img" aria-label="Workers holding produce" style="width:200px;height:168px;background:var(--g-worker)"></div></div>
  </section>
  <section class="sec" style="height:340px;padding-top:40px">
    <div class="row"><div class="ph" role="img" aria-label="Headquarters building exterior" style="width:200px;height:184px;background:var(--g-brick)"></div>
    <div class="col"><div class="eb">Our story</div><div class="h3" style="font-size:12px">One company, from the seedling to the shelf.</div><p class="p" style="margin-top:6px">We began with a small flock and added farming, processing and distribution as each step proved itself. Today every product we sell is grown or made by our own people.</p><p class="p" style="margin-top:6px">That control is why buyers trust our specifications and why families trust our packs.</p><div class="stats"><div class="stat"><b>3</b><span>Product lines</span></div><div class="stat"><b>36<sup>+</sup></b><span>States served</span></div></div></div></div>
  </section>
  <section class="sec cream" style="height:412px;padding-top:48px">
    <div class="row"><div class="col"><div class="eb">Purpose</div><div class="h2">Mission, vision and the values in between.</div></div><div class="col"><p class="p" style="margin-top:32px">What we stand for, in plain words.</p></div></div>
    <div class="row" style="margin-top:20px"><div class="col card"><div class="ic"></div><div class="h3">Our mission</div><p class="p">To produce safe, premium food through integrated and sustainable farming.</p></div><div class="col card"><div class="ic"></div><div class="h3">Our vision</div><p class="p">To be Africa's most trusted integrated food company.</p></div></div>
    <div class="row" style="margin-top:16px"><div class="col"><div class="h3">Integrity</div><p class="p">We do what we say.</p></div><div class="col"><div class="h3">Quality</div><p class="p">No shortcuts.</p></div><div class="col"><div class="h3">Sustainability</div><p class="p">Care for land.</p></div><div class="col"><div class="h3">Innovation</div><p class="p">Always improving.</p></div></div>
  </section>
  <section class="sec" style="height:360px;padding-top:40px">
    <div class="row"><div class="ph" role="img" aria-label="Portrait of the managing director" style="width:200px;height:240px;background:var(--g-portrait)"></div>
    <div class="col"><div class="eb">From the MD</div><div class="h3" style="font-size:10px">"Agriculture is more than a business. It is an opportunity to nourish lives, create meaningful employment and strengthen local economies."</div><p class="p" style="margin-top:8px">We built every stage ourselves so we can stand behind every pack. Our aim is simple: food Nigerians can trust, made to a standard the world would recognise.</p><p class="p" style="margin-top:6px">We are proud of where we come from, and serious about where we are going.</p><div class="h3" style="margin-top:8px">Emeka Dalton</div><p class="p">Managing Director</p></div></div>
  </section>
  <section class="sec" style="height:260px">
    <div class="row"><div class="col"><div class="eb">Leadership</div><div class="h3" style="font-size:12px">The people accountable for it.</div></div><p class="p" style="width:180px;margin-top:14px">A small executive team, close to the operation.</p></div>
    <div class="row" style="margin-top:14px">
      <div class="col"><div class="ph" role="img" aria-label="Portrait of leadership member" style="height:96px;background:var(--g-portrait)"></div><div class="h3" style="margin-top:4px">Emeka Dalton</div><p class="p">Managing Director</p></div>
      <div class="col"><div class="ph" role="img" aria-label="Portrait of leadership member" style="height:96px;background:var(--g-portrait)"></div><div class="h3" style="margin-top:4px">Amara Quist</div><p class="p">Finance Director</p></div>
      <div class="col"><div class="ph" role="img" aria-label="Portrait of leadership member" style="height:96px;background:var(--g-portrait)"></div><div class="h3" style="margin-top:4px">Tunde Rallis</div><p class="p">Operations Director</p></div>
    </div>
  </section>
  <section class="sec" style="height:500px;padding-top:56px">
    <div class="row"><div class="col"><div class="eb">Timeline</div><div class="h3" style="font-size:12px">How the value chain came together.</div><p class="p" style="margin-top:6px">Each step was added once the last one ran to standard.</p><div class="ph" role="img" aria-label="Workers sorting harvest" style="height:104px;margin-top:12px;background:var(--g-worker)"></div></div>
    <div class="col" style="border-left:1.5px solid var(--leaf);padding-left:12px"><p class="p"><b>Layer farm opens</b><br>First flock housed and eggs sold locally.</p><p class="p" style="margin-top:8px"><b>Feed mill</b><br>Own feed for consistent quality.</p><p class="p" style="margin-top:8px"><b>Plantain farms</b><br>Owned and outgrower land planted.</p><p class="p" style="margin-top:8px"><b>Processing plant</b><br>Chips and honey lines installed.</p><p class="p" style="margin-top:8px"><b>Fleet &amp; hubs</b><br>National delivery network.</p><p class="p" style="margin-top:8px"><b>Innovation</b><br>New products in trial with partners.</p></div></div>
  </section>
  <section class="sec" style="height:180px">
    <div class="cta"><div class="row"><div class="col"><div class="eb" style="color:#9fc98a">Company profile</div><div class="h3" style="font-size:12px">The full company profile, in one document.</div><p class="p">History, capacity, products and governance in one PDF.</p></div><div class="btns"><span class="btn">Download profile →</span></div></div></div>
  </section>
  <footer class="foot"><div class="fc"><b class="logo lt">Tallvex</b><br>Morrowdale Farms Limited. Premium food grown, made and delivered in Nigeria.<span class="fin">Your email →</span></div><div class="fc"><i>Company</i>About<br>Our business<br>Sustainability<br>Careers</div><div class="fc"><i>Products</i>Premium eggs<br>Plantain chips<br>Pure honey</div><div class="fc"><i>Visit</i>Harbour Row, Lagos<br>+234 700 000 0000<br>hello@tallvex.example</div></footer>
</div>

<!-- PRODUCTS -->
<div class="page" style="left:1047px;top:18px;height:2484px">
  <div class="nav"><span class="logo">Tallvex</span><span class="links">Home About Products Business Sustainability Careers News Contact</span><span class="navbtn">Contact us</span></div>
  <section class="sec hero" style="height:260px">
    <div class="row"><div class="col" style="padding-top:48px"><div class="eb">Products</div><div class="h1">Three lines. One standard.</div><p class="p" style="margin-top:8px">Eggs, chips and honey, each made to the same rules from farm to pack.</p><div class="row" style="margin-top:8px;gap:6px"><span class="chip">Premium eggs</span><span class="chip">Plantain chips</span><span class="chip">Pure honey</span></div></div>
    <div class="ph" role="img" aria-label="Plantain chips packs" style="width:192px;height:160px;background:var(--g-chips)"></div></div>
  </section>
  <section class="sec" style="height:380px;padding-top:48px">
    <div class="row"><div class="col"><div class="eb">Eggs</div><div class="h2" style="font-size:16px">Premium brown eggs</div><p class="p" style="margin-top:6px">From our own flocks, graded, cleaned and sealed within a day of laying.</p><ul class="bul" style="margin-top:6px"><li>Grade AA, single origin</li><li>Vitamin-rich feed</li><li>Batch coded for traceability</li></ul><div class="row" style="margin-top:10px;gap:6px"><span class="chip">6</span><span class="chip">12</span><span class="chip">15</span><span class="chip">30</span></div><div class="btns"><span class="btn">Order at trade volume →</span></div></div>
    <div class="ph" role="img" aria-label="Egg packs" style="width:208px;height:176px;background:var(--g-eggs)"></div></div>
  </section>
  <section class="sec" style="height:380px">
    <div class="row"><div class="ph" role="img" aria-label="Plantain chips packs" style="width:208px;height:184px;background:var(--g-chips)"></div>
    <div class="col"><div class="eb">Snacks</div><div class="h2" style="font-size:16px">Crispy plantain chips</div><p class="p" style="margin-top:6px">Sliced from our own plantain, fried fresh in small batches and sealed for crunch.</p><ul class="bul" style="margin-top:6px"><li>No artificial colour</li><li>Sweet and spicy flavours</li><li>Nitrogen-flushed packs</li></ul><div class="row" style="margin-top:10px;gap:6px"><span class="chip">60g</span><span class="chip">270g</span><span class="chip">400g</span></div><div class="btns"><span class="btn" style="background:var(--green)">Request a trade price →</span></div></div></div>
  </section>
  <section class="sec" style="height:360px">
    <div class="row"><div class="col"><div class="eb">Honey</div><div class="h2" style="font-size:16px">Pure honey</div><p class="p" style="margin-top:6px">Raw honey from partner beekeepers, filtered, never heated, bottled at our plant.</p><ul class="bul" style="margin-top:6px"><li>100% pure, no added sugar</li><li>Tested for moisture</li><li>Tamper-proof jars</li></ul><div class="row" style="margin-top:10px;gap:6px"><span class="chip">250g</span><span class="chip">500g</span></div><div class="btns"><span class="btn" style="background:var(--green)">Stock honey →</span></div></div>
    <div style="width:200px;display:grid;gap:8px"><div class="ph" role="img" aria-label="Honey jars" style="height:104px;background:var(--g-honey)"></div><div class="ph" role="img" aria-label="Honeycomb" style="height:72px;background:var(--g-honey)"></div></div></div>
  </section>
  <section class="sec onimg" style="height:260px;background:linear-gradient(120deg,#0c3322 45%,#3c4a40);border-radius:50% 50% 0 0/40px 40px 0 0;padding-top:56px" role="img" aria-label="Production hall behind text">
    <div class="eb" style="color:#9fc98a">Manufacturing</div>
    <div class="h2" style="font-size:17px">Made the same way every day, at scale.</div>
    <p class="p" style="margin-top:4px">Consistent pack sizes for homes, retail and trade.</p>
    <div class="stats"><div class="stat"><b>400g</b><span>Family pack</span></div><div class="stat"><b>270g</b><span>Share pack</span></div><div class="stat"><b>60g</b><span>Single serve</span></div></div>
  </section>
  <section class="sec dark down" style="height:340px;border-radius:0 0 50% 50%/0 0 40px 40px;padding-top:40px">
    <div class="row"><div class="col"><div class="eb">Pipeline</div><div class="h2" style="font-size:17px">What we are working on next.</div></div><div class="col"><p class="p" style="margin-top:20px">New products in trial with trade partners before launch.</p></div></div>
    <div class="row" style="margin-top:20px"><div class="col card"><div class="h3">Extended snack range</div><p class="p">New flavours and sizes.</p></div><div class="col card"><div class="h3">Value-added produce</div><p class="p">Processed egg products.</p></div><div class="col card"><div class="h3">Export-ready formats</div><p class="p">For regional markets.</p></div></div>
    <div class="btns"><span class="btn" style="background:#fff;color:var(--green)">Talk to product team →</span></div>
  </section>
  <section class="sec" style="height:280px;padding-top:48px">
    <div class="row"><div class="col"><div class="eb">Trade</div><div class="h3" style="font-size:12px">Specifications, lead times and delivery, agreed up front.</div><p class="p" style="margin-top:6px">We supply retailers, hotels and distributors on fixed terms and schedules.</p><div class="btns"><span class="btn">Get a trade quote →</span><span class="btn ghost">Spec sheets</span></div></div>
    <div class="ph" role="img" aria-label="Supermarket aisle with stocked shelves" style="width:192px;height:120px;background:var(--g-shelf)"></div></div>
  </section>
  <footer class="foot"><div class="fc"><b class="logo lt">Tallvex</b><br>Morrowdale Farms Limited. Premium food grown, made and delivered in Nigeria.<span class="fin">Your email →</span></div><div class="fc"><i>Company</i>About<br>Our business<br>Sustainability<br>Careers</div><div class="fc"><i>Products</i>Premium eggs<br>Plantain chips<br>Pure honey</div><div class="fc"><i>Visit</i>Harbour Row, Lagos<br>+234 700 000 0000<br>hello@tallvex.example</div></footer>
</div>

</div>
</body>
</html>
```